Gobal construction supply company needs new business card design

I need a business card design for my global supply company using an existing logo. i will be looking to print these on rounded corner cards with the black background version of my logo on the back. on the front white background, my logo again and my simple details.

```html
<!DOCTYPE html>
<html lang="en">
<head>
<meta charset="utf-8">
<title>Meridian Build Supply – Business Card</title>
<link rel="stylesheet" href="https://fonts.googleapis.com/css2?family=Montserrat:wght@500;700&display=swap">
<style>
  :root {
    --bg: #3a3a3c;
    --card-white: #ffffff;
    --card-black: #0d0d0d;
    --brand-red: #d9000d;
    --ink: #111111;
    --rule-blue: #1a2f7a;
    --emboss: #2b2b2b;
  }
  * { box-sizing: border-box; margin: 0; padding: 0; }
  html, body { width: 1200px; height: 1000px; overflow: hidden; }
  body {
    background: var(--bg);
    font-family: "Montserrat", sans-serif;
    display: flex; flex-direction: column; align-items: center; justify-content: center;
    gap: 60px;
  }
  .card {
    position: relative;
    width: 620px; height: 354px;
    border-radius: 26px;
    overflow: hidden;
  }
  .card-back { background: var(--card-black); display: flex; align-items: center; justify-content: center; }
  .brand {
    display: flex; align-items: center; gap: 12px;
    font-weight: 700; letter-spacing: 0.5px; white-space: nowrap;
  }
  .brand-dot { width: 14px; height: 14px; border-radius: 50%; background: var(--brand-red); }
  .card-back .brand { font-size: 30px; color: var(--emboss); }
  .card-back .brand-dot { width: 18px; height: 18px; background: var(--emboss); }

  .card-front { background: var(--card-white); color: var(--ink); }
  .card-front .brand { position: absolute; top: 62px; right: 40px; font-size: 21px; color: var(--ink); }
  .person { position: absolute; top: 44px; left: 40px; }
  .person-name { color: var(--brand-red); font-weight: 700; font-size: 22px; letter-spacing: 0.3px; }
  .person-title { font-weight: 500; font-size: 11px; margin-top: 2px; }
  .divider { position: absolute; top: 122px; left: 40px; right: 40px; height: 1.5px; background: var(--rule-blue); }
  .contacts { position: absolute; top: 138px; left: 40px; list-style: none; font-size: 14px; font-weight: 500; }
  .contacts li { display: flex; align-items: center; gap: 8px; line-height: 22px; }
  .contacts svg { width: 11px; height: 11px; fill: var(--brand-red); }
  .contacts .accent { color: var(--brand-red); }
  .address { position: absolute; top: 150px; right: 40px; text-align: right; font-size: 14px; font-weight: 500; line-height: 20px; }
  .band { position: absolute; left: 0; bottom: 0; width: 620px; height: 70px; }
</style>
</head>
<body>
  <div class="card card-back">
    <div class="brand"><span>MERIDIAN BUILD SUPPLY</span><span class="brand-dot"></span></div>
  </div>

  <div class="card card-front">
    <div class="person">
      <div class="person-name">DANIEL MARSH</div>
      <div class="person-title">Managing Director</div>
    </div>
    <div class="brand"><span>MERIDIAN BUILD SUPPLY</span><span class="brand-dot"></span></div>
    <div class="divider"></div>
    <ul class="contacts">
      <li><svg viewBox="0 0 10 10"><path d="M2 0.5 L4 2.5 L3 3.8 C3.8 5.3 4.7 6.2 6.2 7 L7.5 6 L9.5 8 L8 9.5 C4 9 1 6 0.5 2 Z"/></svg>+1 (555) 014 2281</li>
      <li><svg viewBox="0 0 10 10"><path d="M2.5 0 H7.5 V10 H2.5 Z M3.3 1 V8 H6.7 V1 Z"/></svg>+1 (555) 014 2281</li>
      <li><svg viewBox="0 0 10 10"><path d="M0 2 H10 V8.5 H0 Z M0.8 2.6 L5 5.6 L9.2 2.6 Z"/></svg>dan@meridianbs.com</li>
      <li><svg viewBox="0 0 10 10"><circle cx="5" cy="5" r="5"/></svg>www.<span class="accent">meridianbs</span>.com</li>
    </ul>
    <div class="address">2150 Alder Lane,<br>Westbrook<br>City, OK 74012</div>
    <svg class="band" viewBox="0 0 620 70" aria-hidden="true">
      <path d="M0,18 L230,18 C252,18 258,6 280,6" fill="none" stroke="#111" stroke-width="5"/>
      <path d="M0,30 L240,30 C266,30 270,14 300,14 L620,14 L620,70 L0,70 Z" fill="#d9000d"/>
    </svg>
  </div>
</body>
</html>
```